Oil and Gas Exploration and Production company needs a business card design

We need a business card design using our logo and colors in the logo. We want a mainstream design.

```html
<!DOCTYPE html>
<html lang="en">
<head>
<meta charset="utf-8">
<title>Corvan Oil &amp; Gas — Business Card</title>
<link rel="stylesheet" href="https://fonts.googleapis.com/css2?family=Lato:wght@400;700;900&family=Roboto:wght@500;700&display=swap">
<style>
  :root {
    --stage: #3a3a3a;
    --card-black: #141414;
    --card-white: #ffffff;
    --gold: #c99a2e;
    --ink: #2b2b2b;
    --ink-soft: #3d3d3d;
    --rule: #a8a8a8;
  }
  * { margin: 0; padding: 0; box-sizing: border-box; }
  html, body {
    width: 1200px; height: 960px; overflow: hidden;
    background: var(--stage);
  }
  .canvas {
    position: relative; width: 1200px; height: 960px;
    display: flex; flex-direction: column; align-items: center;
    justify-content: center; gap: 60px;
  }
  .card {
    width: 665px; height: 380px; position: relative;
    box-shadow: 0 12px 30px rgba(0,0,0,.45);
  }
  .card--back {
    background: var(--card-black);
    display: flex; align-items: center; justify-content: center;
  }
  .card--front { background: var(--card-white); }

  .brand {
    display: flex; align-items: center; gap: 14px;
    font-family: "Lato", sans-serif; font-weight: 900;
    letter-spacing: 0.2px; white-space: nowrap;
  }
  .brand__dot { width: 34px; height: 34px; border-radius: 50%; flex: none; }
  .brand--back { color: #ffffff; font-size: 46px; }
  .brand--back .brand__dot { background: var(--gold); }
  .brand--front {
    position: absolute; left: 44px; top: 166px;
    color: var(--card-black); font-size: 31px;
  }
  .brand--front .brand__dot { width: 26px; height: 26px; background: var(--gold); }

  .divider {
    position: absolute; left: 352px; top: 118px;
    width: 2px; height: 176px; background: var(--rule);
  }

  .contact {
    position: absolute; left: 384px; top: 116px;
    font-family: "Lato", sans-serif; color: var(--ink-soft);
  }
  .contact__name {
    font-family: "Roboto", sans-serif; font-weight: 700;
    font-size: 29px; color: var(--gold); line-height: 1.05;
  }
  .contact__title {
    font-family: "Roboto", sans-serif; font-weight: 500;
    font-size: 20px; color: var(--ink); margin-top: 2px;
  }
  .contact__address {
    font-size: 16px; line-height: 1.35; margin-top: 16px;
  }
  .contact__list { list-style: none; margin-top: 14px; }
  .contact__item {
    display: flex; align-items: center; gap: 10px;
    font-size: 17px; line-height: 1.5;
  }
  .contact__icon { width: 15px; height: 15px; flex: none; fill: var(--gold); }
</style>
</head>
<body>
<main class="canvas">
  <section class="card card--back" aria-label="Card back">
    <div class="brand brand--back"><span class="brand__dot"></span>Corvan Oil &amp; Gas</div>
  </section>

  <section class="card card--front" aria-label="Card front">
    <div class="brand brand--front"><span class="brand__dot"></span>Corvan Oil &amp; Gas</div>
    <div class="divider"></div>
    <div class="contact">
      <p class="contact__name">Daniel Hart</p>
      <p class="contact__title">President</p>
      <p class="contact__address">Level 5, 120 Harbour Lane<br>Brisbane, QLD 4000</p>
      <ul class="contact__list">
        <li class="contact__item">
          <svg class="contact__icon" viewBox="0 0 24 24" aria-hidden="true"><path d="M6.6 10.8a15.1 15.1 0 0 0 6.6 6.6l2.2-2.2c.3-.3.7-.4 1-.2 1.1.4 2.3.6 3.6.6.6 0 1 .4 1 1V20c0 .6-.4 1-1 1A17 17 0 0 1 3 4c0-.6.4-1 1-1h3.5c.6 0 1 .4 1 1 0 1.3.2 2.5.6 3.6.1.3 0 .7-.2 1z"/></svg>
          555 014 2290
        </li>
        <li class="contact__item">
          <svg class="contact__icon" viewBox="0 0 24 24" aria-hidden="true"><path d="M2 5h20v14H2z M2 5l10 7 10-7" /><path d="M2 5l10 7 10-7v2l-10 7L2 7z" fill="#fff"/></svg>
          hello@northbend.com
        </li>
        <li class="contact__item">
          <svg class="contact__icon" viewBox="0 0 24 24" aria-hidden="true"><circle cx="12" cy="12" r="10"/><path d="M2 12h20M12 2c3 3 3 17 0 20M12 2c-3 3-3 17 0 20M4 7h16M4 17h16" stroke="#fff" stroke-width="1.4" fill="none"/></svg>
          www.northbend.com
        </li>
      </ul>
    </div>
  </section>
</main>
</body>
</html>
```